KBT Business Cards

We require business cards for our business. We would like a matte black back to the card, with our logo centred in the middle. The front side of the card is open to design.

Target Market(s)

Clients looking for legal services (professional)

Industry/Entity Type

Legal

Contact Information for Business Card

Doran Kelbrath
Partner
Mobile: 0461 738 524
Email: doran@kbtlaw.co
Website: www.kbtlaw.co
Level 3, 118 Wendmore Street
Sydney NSW 2000

Font styles to use
Other font styles liked:
• Avenir

Colors
f04a50
ffffff
1b1b1b

Requirements
Must have
• Black back with logo included in the centre of the card.
• Our font is Avenir.

```html
<!DOCTYPE html>
<html lang="en">
<head>
<meta charset="UTF-8">
<title>KBT Legal – Business Cards</title>
<link href="https://fonts.googleapis.com/css2?family=Nunito+Sans:wght@400;600;700&display=swap" rel="stylesheet">
<style>
  :root {
    --brand-red: #c2213f;
    --ink: #1b1b1b;
    --paper: #ffffff;
    --card-black: #1b1b1b;
    --backdrop: #e9e4dc;
    --muted: #3a3a3a;
  }
  * { box-sizing: border-box; margin: 0; padding: 0; }
  html, body {
    width: 1200px; height: 942px; overflow: hidden;
    background: var(--backdrop);
    font-family: "Nunito Sans", "Avenir", sans-serif;
  }
  .sheet {
    width: 1200px; height: 942px;
    display: flex; flex-direction: column;
    align-items: center; justify-content: center; gap: 56px;
  }
  .card {
    width: 700px; height: 400px;
    border-radius: 18px;
    position: relative;
    box-shadow: 0 10px 28px rgba(0,0,0,0.18);
  }
  .card--front { background: var(--paper); color: var(--ink); }
  .card--back { background: var(--card-black); display: flex; align-items: center; justify-content: center; }

  .identity { position: absolute; left: 48px; top: 44px; }
  .identity__name { color: var(--brand-red); font-weight: 700; font-size: 26px; letter-spacing: 0.2px; }
  .identity__role { font-size: 17px; color: var(--muted); margin-top: 2px; }

  .contacts { position: absolute; left: 48px; bottom: 44px; list-style: none; }
  .contacts li { display: flex; align-items: center; gap: 10px; font-size: 16px; color: var(--muted); line-height: 1.75; }
  .contacts svg { width: 15px; height: 15px; flex: none; }

  .address { position: absolute; right: 48px; top: 48px; text-align: right; font-size: 16px; color: var(--muted); line-height: 1.5; }

  .wordmark { display: flex; align-items: center; gap: 14px; }
  .wordmark__square { width: 22px; height: 22px; background: var(--brand-red); }
  .wordmark__name { font-weight: 700; letter-spacing: 1.5px; }
  .card--front .wordmark { position: absolute; right: 48px; bottom: 44px; }
  .card--front .wordmark__name { font-size: 30px; color: var(--ink); }
  .card--back .wordmark__square { width: 34px; height: 34px; }
  .card--back .wordmark__name { font-size: 48px; color: var(--paper); }
</style>
</head>
<body>
<main class="sheet">
  <section class="card card--front" aria-label="Card front">
    <div class="identity">
      <p class="identity__name">Doran Kelbrath</p>
      <p class="identity__role">Partner</p>
    </div>

    <ul class="contacts">
      <li>
        <svg viewBox="0 0 16 16" aria-hidden="true"><circle cx="8" cy="8" r="8" fill="var(--brand-red)"/><path d="M5.3 4.2l1.4 1.6-.7 1.1c.5 1 1.3 1.8 2.3 2.3l1.1-.7 1.6 1.4-.9 1.4C7.6 11 5 8.4 4.2 5.1z" fill="#fff"/></svg>
        0461 738 524
      </li>
      <li>
        <svg viewBox="0 0 16 16" aria-hidden="true"><rect width="16" height="16" rx="2" fill="var(--brand-red)"/><rect x="3.5" y="5" width="9" height="6.5" fill="none" stroke="#fff" stroke-width="1.1"/><path d="M3.5 5l4.5 3.6L12.5 5" fill="none" stroke="#fff" stroke-width="1.1"/></svg>
        doran@kbtlaw.co
      </li>
      <li>
        <svg viewBox="0 0 16 16" aria-hidden="true"><circle cx="8" cy="8" r="8" fill="var(--brand-red)"/><circle cx="8" cy="8" r="4.3" fill="none" stroke="#fff" stroke-width="1"/><path d="M3.7 8h8.6M8 3.7c-2 2.4-2 6.2 0 8.6M8 3.7c2 2.4 2 6.2 0 8.6" fill="none" stroke="#fff" stroke-width="0.9"/></svg>
        www.kbtlaw.co
      </li>
    </ul>

    <address class="address" style="font-style:normal">
      Level 3, 118 Wendmore Street<br>
      Sydney NSW 2000
    </address>

    <div class="wordmark">
      <span class="wordmark__square" aria-hidden="true"></span>
      <span class="wordmark__name">KBT LEGAL</span>
    </div>
  </section>

  <section class="card card--back" aria-label="Card back">
    <div class="wordmark">
      <span class="wordmark__square" aria-hidden="true"></span>
      <span class="wordmark__name">KBT LEGAL</span>
    </div>
  </section>
</main>
</body>
</html>
```